Veldmark Supplies Business Card

Professional business card that stand out to our potential customers. Front and back with clean modern design

Industry/Entity Type

Oil and gas

Contact Information for Business Card

Name, address, website , office phone and cell number

Requirements
Must have
• Editable files for each employee

```html
<!DOCTYPE html>
<html lang="en">
<head>
<meta charset="utf-8">
<title>Veldmark Supplies Business Card</title>
<link href="https://fonts.googleapis.com/css2?family=Poppins:wght@400;500;600&display=swap" rel="stylesheet">
<style>
  :root {
    --backdrop: #888888;
    --brand-blue: #0cb0d2;
    --brand-red: #ec1f26;
    --paper: #ffffff;
    --ink: #2a2a2a;
  }
  * { margin: 0; padding: 0; box-sizing: border-box; }
  html, body {
    width: 720px; height: 1200px; overflow: hidden;
    background: var(--backdrop);
    font-family: "Poppins", sans-serif;
  }
  .canvas { position: relative; width: 720px; height: 1200px; }
  .card {
    position: absolute; left: 60px; width: 600px; height: 343px; overflow: hidden;
  }
  .card-front { top: 207px; background: var(--brand-blue); color: var(--paper); }
  .card-back { top: 650px; background: var(--paper); color: var(--ink); }

  .front-brand {
    position: absolute; left: 0; right: 0; top: 120px;
    display: flex; align-items: center; justify-content: center; gap: 12px;
  }
  .brand-square { width: 22px; height: 22px; background: var(--paper); }
  .front-brand .brand-name {
    font-size: 26px; font-weight: 600; letter-spacing: 1px; text-transform: uppercase;
  }
  .front-web {
    position: absolute; left: 0; right: 0; top: 283px;
    display: flex; align-items: center; justify-content: center; gap: 8px;
    font-size: 12px; letter-spacing: 1px;
  }
  .front-web svg { width: 14px; height: 14px; }

  .back-brand {
    position: absolute; left: 60px; top: 158px; width: 210px;
    display: flex; align-items: center; justify-content: center; gap: 8px;
  }
  .back-brand .brand-square { width: 14px; height: 14px; background: var(--brand-red); }
  .back-brand .brand-name {
    color: var(--brand-red); font-size: 15px; font-weight: 600; letter-spacing: 0.5px;
    text-transform: uppercase;
  }

  .holder-name {
    position: absolute; left: 328px; top: 50px;
    color: var(--brand-blue); font-size: 25px; font-weight: 600; letter-spacing: 2px;
  }
  .holder-title {
    position: absolute; left: 328px; top: 84px;
    font-size: 12px; font-weight: 500; letter-spacing: 0.8px;
  }
  .address {
    position: absolute; left: 322px; top: 157px;
    font-size: 12px; line-height: 17px; letter-spacing: 1px; font-style: normal;
  }
  .contacts { position: absolute; left: 322px; top: 230px; list-style: none; }
  .contacts li {
    display: flex; align-items: center; height: 24px;
    font-size: 12px; letter-spacing: 1px;
  }
  .contacts svg { width: 15px; height: 15px; margin-right: 16px; }

  .brand-stripe { position: absolute; left: 0; bottom: 0; width: 600px; height: 15px; }
</style>
</head>
<body>
<main class="canvas">
  <section class="card card-front" aria-label="Card front">
    <div class="front-brand">
      <span class="brand-square"></span>
      <span class="brand-name">Veldmark Supplies</span>
    </div>
    <div class="front-web">
      <svg viewBox="0 0 16 16" aria-hidden="true"><circle cx="8" cy="8" r="7.5" fill="#fff"/><path d="M4 3.5c2 .5 2.5 2 1.5 3S3 8 4 10s3 1 3 3M10 2.5c-1 1.5.5 3 2 3s2 1.5 2.5 2.5M9.5 9c1.5 0 2.5 1 2 2.5s-1.5 2-2.5 3" stroke="#0cb0d2" stroke-width="1.5" fill="none"/></svg>
      <span>www.veldmarksupplies.com</span>
    </div>
  </section>

  <section class="card card-back" aria-label="Card back">
    <div class="back-brand">
      <span class="brand-square"></span>
      <span class="brand-name">Veldmark Supplies</span>
    </div>
    <h1 class="holder-name">Tobias R. Hallen</h1>
    <p class="holder-title">Managing Director</p>
    <address class="address">410 N.Crestline Suite 5<br>Midland, Tx 79701</address>
    <ul class="contacts">
      <li>
        <svg viewBox="0 0 16 16" aria-hidden="true"><path d="M1 6c0-2 3-3.5 7-3.5S15 4 15 6v1.5h-3.5V6h-7v1.5H1z M4 8h8l2 6H2z" fill="#0cb0d2"/><circle cx="8" cy="11" r="1.6" fill="#fff"/></svg>
        <span>(555)014-0283</span>
      </li>
      <li>
        <svg viewBox="0 0 16 16" aria-hidden="true"><rect x="1" y="3" width="14" height="10" fill="#0cb0d2"/><path d="M1 3l7 6 7-6M1 13l5-5M15 13l-5-5" stroke="#fff" stroke-width="1" fill="none"/></svg>
        <span>sales@veldmarksupplies.com</span>
      </li>
      <li>
        <svg viewBox="0 0 16 16" aria-hidden="true"><circle cx="8" cy="8" r="7.5" fill="#0cb0d2"/><path d="M4 3.5c2 .5 2.5 2 1.5 3S3 8 4 10s3 1 3 3M10 2.5c-1 1.5.5 3 2 3s2 1.5 2.5 2.5M9.5 9c1.5 0 2.5 1 2 2.5s-1.5 2-2.5 3" stroke="#fff" stroke-width="1.5" fill="none"/></svg>
        <span>www.veldmarksupplies.com</span>
      </li>
    </ul>
    <svg class="brand-stripe" viewBox="0 0 600 15" preserveAspectRatio="none" aria-hidden="true">
      <polygon points="0,0 300,0 294,15 0,15" fill="#ec1f26"/>
      <polygon points="307,0 600,0 600,15 301,15" fill="#0cb0d2"/>
    </svg>
  </section>
</main>
</body>
</html>
```